Moravel Aesthetic Doctor

I require an elegant, luxurious looking business card for my aesthetic business. I am a doctor and that will set me aside from competitors. I am planning to provide home and spa based treatments to clients with high expectations. I have attached my logo.

```html
<!DOCTYPE html>
<html lang="en">
<head>
<meta charset="UTF-8">
<title>Moravel Aesthetic Doctor – Business Card</title>
<link rel="stylesheet" href="https://fonts.googleapis.com/css2?family=Open+Sans:wght@300;400&display=swap">
<style>
  :root {
    --backdrop: #3a3a3c;
    --card: #202022;
    --ink: #f2f2f2;
    --muted: #b9bcc2;
    --sky: #5ab4e8;
    --sky-deep: #1f86cc;
    --sky-pale: #9fd3f2;
  }
  * { box-sizing: border-box; margin: 0; padding: 0; }
  html, body { width: 799px; height: 1200px; overflow: hidden; }
  body {
    background: var(--backdrop);
    font-family: "Open Sans", Arial, sans-serif;
    color: var(--ink);
    display: flex;
    flex-direction: column;
    justify-content: space-evenly;
    align-items: center;
  }
  .card {
    position: relative;
    width: 660px;
    height: 377px;
    background: var(--card);
    border-radius: 4px;
    overflow: hidden;
    box-shadow: 0 14px 30px rgba(0,0,0,.45);
  }
  .wordmark {
    font-weight: 300;
    color: var(--muted);
    letter-spacing: 2px;
    text-transform: uppercase;
    line-height: 1.15;
  }
  .wordmark__badge {
    display: inline-block;
    width: 44px; height: 44px;
    border: 2px solid var(--muted);
    border-radius: 50%;
    vertical-align: middle;
    margin-right: 16px;
  }

  /* Front */
  .front__brand {
    position: absolute;
    top: 62px; left: 0; right: 0;
    display: flex; align-items: center; justify-content: center;
  }
  .front__brand .wordmark { font-size: 30px; }
  .front__rule {
    position: absolute; left: 0; right: 0; top: 176px;
    height: 14px; background: var(--sky);
  }
  .front__services {
    position: absolute; top: 204px; left: 0; right: 0;
    text-align: center; font-size: 17px; line-height: 1.55;
  }
  .front__band {
    position: absolute; left: 0; right: 0; top: 272px;
    height: 40px; background: var(--sky);
    display: flex; align-items: center; justify-content: center;
    font-size: 17px; letter-spacing: 1px; color: #fff;
  }

  /* Back */
  .back__brand { position: absolute; top: 40px; left: 40px; }
  .back__brand .wordmark { font-size: 24px; }
  .back__name {
    position: absolute; top: 118px; left: 40px;
    font-size: 20px; font-weight: 300; color: var(--muted);
  }
  .back__name small { font-size: 10px; color: var(--sky); margin-left: 4px; }
  .back__credential {
    position: absolute; top: 148px; left: 40px;
    font-size: 13px; color: var(--sky); line-height: 1.35;
  }
  .contact {
    position: absolute; top: 222px; left: 40px;
    list-style: none; font-size: 13px; color: var(--ink);
  }
  .contact li { display: flex; align-items: center; gap: 10px; height: 24px; }
  .contact svg { width: 13px; height: 13px; fill: var(--muted); }
  .social { display: inline-flex; gap: 5px; margin-left: 6px; }
  .social span { width: 14px; height: 14px; border-radius: 50%; background: var(--muted); }
  .back__art {
    position: absolute; top: 60px; right: 0;
    width: 300px; height: 317px;
    background: linear-gradient(160deg, var(--sky-deep) 0%, var(--sky) 55%, var(--sky-pale) 100%);
    border-radius: 60% 0 0 40%;
  }
</style>
</head>
<body>
  <section class="card front" aria-label="Card front">
    <div class="front__brand">
      <span class="wordmark__badge"></span>
      <span class="wordmark">Moravel<br>Aesthetic Doctor</span>
    </div>
    <div class="front__rule"></div>
    <p class="front__services">
      Dermal Injectables &nbsp;|&nbsp; Plasma Facials &nbsp;|&nbsp; Microneedling<br>
      Skin Boosters &nbsp;|&nbsp; Excessive Sweating
    </p>
    <div class="front__band">HOME AND SPA BASED TREATMENTS</div>
  </section>

  <section class="card back" aria-label="Card back">
    <div class="back__brand"><span class="wordmark">Moravel<br>Aesthetic Doctor</span></div>
    <p class="back__name">Dr Lena Varro<small>MRCPCH MD</small></p>
    <p class="back__credential">Australasian Diploma of<br>Aesthetic Medicine</p>
    <ul class="contact">
      <li><svg viewBox="0 0 24 24"><path d="M6.6 10.8a15 15 0 0 0 6.6 6.6l2.2-2.2a1 1 0 0 1 1-.25 11 11 0 0 0 3.6.6 1 1 0 0 1 1 1V20a1 1 0 0 1-1 1A17 17 0 0 1 3 4a1 1 0 0 1 1-1h3.5a1 1 0 0 1 1 1 11 11 0 0 0 .6 3.6 1 1 0 0 1-.25 1z"/></svg>0800 555 019</li>
      <li><svg viewBox="0 0 24 24"><path d="M2 5h20v14H2zm2 2v.5l8 5 8-5V7l-8 5z"/></svg>lena@moravel.co.nz</li>
      <li><svg viewBox="0 0 24 24"><path d="M12 2a10 10 0 1 0 0 20 10 10 0 0 0 0-20zm6.9 9h-3a15 15 0 0 0-1.4-6 8 8 0 0 1 4.4 6zM12 4c.9 1.3 1.7 3.8 1.9 7h-3.8C10.3 7.8 11.1 5.3 12 4zM9.5 5a15 15 0 0 0-1.4 6h-3a8 8 0 0 1 4.4-6zm-4.4 8h3a15 15 0 0 0 1.4 6 8 8 0 0 1-4.4-6zm6.9 7c-.9-1.3-1.7-3.8-1.9-7h3.8c-.2 3.2-1 5.7-1.9 7zm2.5-1a15 15 0 0 0 1.4-6h3a8 8 0 0 1-4.4 6z"/></svg>www.moravel.co.nz &nbsp;|&nbsp; Follow us on:<span class="social"><span></span><span></span></span></li>
    </ul>
    <div class="back__art" role="img" aria-label="Illustration of a profile with flowing blue hair ribbons"></div>
  </section>
</body>
</html>
```